Velour Detailing – Premium Automotive Detailing Studio Website Design

We're launching a premium automotive detailing studio called Velour Detailing, and we’re looking for a clean, minimal, and high-end website design (desktop + mobile version). The studio targets owners of luxury vehicles who care deeply about aesthetics, perfection, and exceptional service.
This project is about more than just showing services , it should feel like a luxury experience from the very first second. The design should be modern, minimalistic, elegant, and clearly aimed at an upscale market.
We’re looking for a designer who can translate our physical studio’s premium interior and architectural feel into a digital presence.
What we want the website to feel like:
Clean and modern
Professional and luxurious
Minimal and not cluttered
Light animations or transitions to add polish
Stylish and cinematic
Design freedom:
We trust your design direction. We are not providing strict color codes or layout instructions, we want you to create what you believe works best based on our brand positioning and target audience. Just keep it premium, modern, and well-organized.
What the website should include:
Hero section with a bold visual (image or video)
About the Studio — a few blocks explaining our story and focus on quality
Service Overview — clearly showing what we offer (detailing, ceramic coating, interior, etc.)
Gallery/Showcase — show off our work with cars, interior, and the space itself
Client Lounge Area — mention comfort, coffee, and waiting space
Testimonials — social proof from satisfied clients
Location & contact section — map, address, contact form
Footer, simple with nav, contact info, and optional social media
Target audience:
Owners of high-end vehicles (Valtrane, Korvel, etc.)
Car collectors and detailing enthusiasts
People looking for premium-level service and presentation
Brands/creators booking our photo studio

```html
<!DOCTYPE html>
<html lang="en">
<head>
<meta charset="UTF-8">
<title>Velour Detailing – Premium Automotive Detailing Studio</title>
<link href="https://fonts.googleapis.com/css2?family=Exo+2:wght@400;500;600&family=Jost:wght@400;500&display=swap" rel="stylesheet">
<style>
:root{
  --ink:#111111;
  --text:#2a2a2a;
  --muted:#555555;
  --line:#4a4a4a;
  --white:#ffffff;
  --panel:rgba(92,92,92,.78);
  --panel-dark:#3b3b3b;
  --footer:#111111;
}
*{box-sizing:border-box;margin:0;padding:0}
html,body{width:1200px;height:4680px;overflow:hidden}
body{background:var(--white);color:var(--text);font-family:"Jost",sans-serif;position:relative}
.section{position:relative;width:1200px;overflow:hidden}
.abs{position:absolute}
.heading{font-family:"Exo 2",sans-serif;font-weight:500;color:var(--ink);text-transform:uppercase;letter-spacing:.5px}
.pill{display:inline-flex;align-items:center;gap:10px;background:var(--ink);color:var(--white);border-radius:10px;font-size:14px;padding:0 14px 0 20px;height:38px;text-decoration:none}
.pill .dot{width:17px;height:17px;border-radius:50%;background:var(--white);display:flex;align-items:center;justify-content:center}
.photo{position:absolute}

/* hero */
.hero{height:600px}
.hero-bg{inset:0;background:
  radial-gradient(ellipse 300px 90px at 600px 520px,rgba(255,255,255,.9),rgba(255,255,255,0)),
  radial-gradient(ellipse 700px 260px at 600px 170px,#f4f4f4 0%,rgba(240,240,240,0) 100%),
  linear-gradient(180deg,#cfcfcf 0%,#e6e6e6 40%,#d8d8d8 60%,#c4c4c4 100%)}
.hero-cars{left:0;right:0;top:340px;height:230px;background:
  radial-gradient(ellipse 190px 120px at 600px 120px,#1a1a1a 0%,#3a3a3a 55%,rgba(60,60,60,0) 100%),
  radial-gradient(ellipse 210px 120px at 200px 120px,#1c1c1c 0%,#444 55%,rgba(70,70,70,0) 100%),
  radial-gradient(ellipse 210px 120px at 1000px 120px,#1c1c1c 0%,#444 55%,rgba(70,70,70,0) 100%),
  radial-gradient(ellipse 120px 110px at 40px 130px,#2a2a2a 0%,rgba(60,60,60,0) 100%)}
.hero-floor{left:0;right:0;top:500px;height:100px;background:linear-gradient(180deg,rgba(150,150,150,.0) 0%,rgba(130,130,130,.55) 45%,#8a8a8a 100%)}
.brand{display:flex;align-items:center;gap:12px;text-decoration:none}
.brand-mark{width:30px;height:30px;background:var(--ink)}
.brand-name{font-family:"Exo 2",sans-serif;font-weight:600;color:var(--ink);line-height:1;text-transform:uppercase}
.brand-name span{display:block;letter-spacing:7px;font-size:15px;margin-top:4px}
.brand-name b{font-weight:600;font-size:30px;letter-spacing:1px}
.site-header{left:65px;top:28px;right:65px;display:flex;justify-content:space-between;align-items:center}
.nav{display:flex;gap:36px;list-style:none}
.nav a{color:var(--ink);text-decoration:none;font-size:19px;text-transform:uppercase}
.nav a.active{text-decoration:underline;text-underline-offset:5px}
.hero-frame{left:187px;top:140px;width:826px;height:149px;border:1.5px solid var(--line);text-align:center;padding-top:22px}
.hero-frame h1{font-size:45px;line-height:1.05}
.hero-frame p{font-size:21px;margin-top:8px;color:var(--ink)}
.hero-cta{left:498px;top:268px}

/* services */
.services{height:678px}
.services h2{left:105px;top:80px;font-size:36px}
.services .lead{left:105px;top:143px;width:810px;font-size:16px;line-height:22px}
.arrow{width:56px;height:56px;border-radius:50%;display:flex;align-items:center;justify-content:center}
.arrow.outline{border:2px solid var(--ink);background:var(--white)}
.arrow.filled{background:var(--ink)}
.service-card{top:244px;width:308px;height:345px;border:1.5px solid var(--line);border-radius:16px}
.service-card .photo{left:15px;top:15px;right:15px;height:262px;border-radius:12px}
.service-card h3{position:absolute;left:0;right:0;bottom:24px;text-align:center;font-size:21px;font-weight:500}

/* about */
.about{height:517px}
.about-bg{inset:0;background:
  radial-gradient(ellipse 120px 50px at 90px 330px,rgba(235,240,245,.95),rgba(200,205,210,0)),
  radial-gradient(ellipse 140px 140px at 460px 290px,#8a8a8a 0%,#3a3a3a 50%,rgba(30,30,30,0) 100%),
  radial-gradient(ellipse 420px 260px at 220px 160px,#6e6e6e 0%,#3a3a3a 55%,rgba(25,25,25,0) 100%),
  linear-gradient(100deg,#2e2e2e 0%,#1a1a1a 45%,#0e0e0e 100%)}
.about-panel{left:593px;top:84px;width:496px;height:349px;background:var(--panel);text-align:center;padding:32px 40px 0}
.about-panel h2{color:var(--white);font-size:36px}
.about-panel p{color:#eaeaea;font-size:16px;line-height:27px;margin-top:14px}
.about-panel .pill{margin-top:12px;background:#0d0d0d}

/* gallery */
.gallery{height:825px}
.gallery h2{left:0;right:0;top:60px;text-align:center;font-size:36px}
.tile{border-radius:14px}
.gallery-cta{left:534px;top:755px}

/* lounge */
.lounge{height:633px}
.lounge h2{left:105px;top:45px;font-size:36px}
.lounge .lead{left:105px;top:118px;width:475px;font-size:16px;line-height:27px}
.amenity{left:105px;display:flex;gap:28px}
.amenity .icon{width:96px;height:96px;border-radius:50%;background:var(--ink);flex:none}
.amenity h3{font-family:"Jost",sans-serif;font-weight:500;font-size:19px;text-transform:uppercase;color:var(--ink);margin-top:8px}
.amenity p{font-size:13.5px;line-height:24px;color:var(--muted);width:320px;margin-top:6px}
.lounge-photo{left:596px;top:260px;width:515px;height:245px;background:
  radial-gradient(ellipse 120px 80px at 150px 110px,#9a5a2e 0%,#6a3c1e 45%,rgba(255,255,255,0) 100%),
  radial-gradient(ellipse 80px 70px at 60px 100px,#1f2a3a 0%,rgba(255,255,255,0) 100%),
  radial-gradient(ellipse 100px 70px at 400px 90px,#a86a3c 0%,#7a4a28 45%,rgba(255,255,255,0) 100%),
  radial-gradient(ellipse 60px 40px at 300px 130px,#222 0%,rgba(255,255,255,0) 100%),
  radial-gradient(ellipse 240px 20px at 250px 225px,rgba(180,180,180,.6),rgba(255,255,255,0))}

/* testimonials */
.testimonials{height:514px}
.testimonials-bg{inset:0;background:
  radial-gradient(ellipse 80px 90px at 80px 130px,#d8d8d8 0%,#7a7a7a 45%,rgba(40,40,40,0) 100%),
  radial-gradient(ellipse 80px 90px at 200px 100px,#cfcfcf 0%,#6a6a6a 45%,rgba(40,40,40,0) 100%),
  radial-gradient(ellipse 300px 160px at 150px 400px,#5a5a5a 0%,rgba(30,30,30,0) 100%),
  linear-gradient(90deg,#2e2e2e 0%,#1c1c1c 40%,#121212 100%)}
.quote-panel{left:578px;top:103px;width:507px;height:305px;background:var(--panel-dark);color:var(--white)}
.quote-panel h2{position:absolute;left:0;right:0;top:18px;text-align:center;color:var(--white);font-size:34px}
.stars{position:absolute;left:44px;top:94px;color:#f2a20c;font-size:17px;letter-spacing:1px}
.review-source{position:absolute;left:442px;top:80px;width:36px;height:36px;border-radius:50%;background:#ffffff}
.quote-panel blockquote{position:absolute;left:44px;top:122px;width:430px;font-size:12.5px;line-height:20px;color:#e2e2e2}
.avatar{position:absolute;left:40px;top:243px;width:44px;height:44px;border-radius:50%;background:#111;color:#fff;font-family:"Exo 2",sans-serif;font-size:15px;display:flex;align-items:center;justify-content:center}
.reviewer{position:absolute;left:102px;top:247px}
.reviewer strong{display:block;font-family:"Exo 2",sans-serif;font-weight:500;font-size:13px;text-transform:uppercase}
.reviewer span{font-size:11px;color:#bdbdbd}
.quote-mark{position:absolute;left:464px;top:236px;font-family:"Exo 2",sans-serif;font-size:54px;line-height:1;color:#fff}
.slide-arrow{width:36px;height:36px;border-radius:50%;background:var(--white);display:flex;align-items:center;justify-content:center}

/* contact */
.contact{height:647px}
.contact h2{left:0;right:0;top:78px;text-align:center;font-size:36px}
.field{left:105px;width:473px;height:40px;border:1.5px solid var(--line);border-radius:12px;font-size:13px;padding:11px 16px;color:var(--ink)}
.field.message{height:107px}
.submit{left:105px;top:504px}
.map-ring{left:675px;top:146px;width:420px;height:410px;border-radius:50%;background:var(--ink)}
.map{left:655px;top:151px;width:400px;height:400px;border-radius:50%;background:
  radial-gradient(ellipse 140px 90px at 200px 230px,#f6f6f6 0%,#eeeeee 60%,rgba(240,240,240,0) 100%),
  radial-gradient(ellipse 120px 90px at 90px 110px,#a6d7a0 0%,rgba(200,230,195,0) 100%),
  radial-gradient(ellipse 140px 100px at 300px 330px,#9fd39a 0%,rgba(200,230,195,0) 100%),
  radial-gradient(circle at 45% 45%,#e4efe0 0%,#cfe6c9 55%,#b5dbb0 100%)}

/* footer */
.footer{height:266px;background:var(--footer);color:var(--white)}
.footer .brand{position:absolute;left:0;right:0;top:60px;justify-content:center}
.footer .brand-mark{background:var(--white);width:38px;height:38px}
.footer .brand-name{color:var(--white)}
.footer .brand-name b{font-size:38px}
.footer .brand-name span{font-size:19px;letter-spacing:9px}
.footer .nav{position:absolute;left:0;right:0;top:162px;justify-content:center;gap:36px}
.footer .nav a{color:var(--white);font-size:19px}
.footer hr{position:absolute;left:105px;right:105px;top:214px;border:0;border-top:1px solid #333}
.copyright{position:absolute;left:0;right:0;top:232px;text-align:center;font-size:12px;color:#9a9a9a}
</style>
</head>
<body>

<header class="section hero">
  <div class="photo hero-bg" role="img" aria-label="Bright white detailing studio with a glossy floor"></div>
  <div class="photo hero-cars" role="img" aria-label="Three dark grey luxury sedans lined up with headlights on"></div>
  <div class="photo hero-floor" role="img" aria-label="Reflections of the cars on the studio floor"></div>
  <div class="abs site-header">
    <a class="brand" href="#"><span class="brand-mark"></span><span class="brand-name"><b>VELOUR</b><span>DETAILING</span></span></a>
    <ul class="nav">
      <li><a class="active" href="#">Home</a></li>
      <li><a href="#">About</a></li>
      <li><a href="#">Services</a></li>
      <li><a href="#">Gallery</a></li>
      <li><a href="#">Testimonials</a></li>
      <li><a href="#">Contact</a></li>
    </ul>
  </div>
  <div class="abs hero-frame">
    <h1 class="heading">Crafted for Automotive Purists</h1>
    <p>Premium detailing for vehicles that deserve nothing less.</p>
  </div>
  <a class="abs pill hero-cta" href="#">Explore Our Services <span class="dot"><svg width="9" height="9" viewBox="0 0 10 10"><path d="M3 1.5 6.5 5 3 8.5" stroke="#111" stroke-width="2" fill="none"/></svg></span></a>
</header>

<section class="section services">
  <h2 class="abs heading">Our Services</h2>
  <p class="abs lead">Sed ut perspiciatis unde omnis iste natus error sit voluptatem accusantium doloremque laudantium, totam rem aperiam,</p>
  <div class="abs arrow outline" style="left:954px;top:116px"><svg width="20" height="20" viewBox="0 0 20 20"><path d="M13 3 6 10l7 7" stroke="#111" stroke-width="2" fill="none"/></svg></div>
  <div class="abs arrow filled" style="left:1034px;top:116px"><svg width="22" height="22" viewBox="0 0 20 20"><path d="M7 3l7 7-7 7" stroke="#fff" stroke-width="2.6" fill="none"/></svg></div>
  <article class="abs service-card" style="left:105px">
    <div class="photo" role="img" aria-label="Brush cleaning a car interior console" style="background:radial-gradient(ellipse 50px 60px at 110px 160px,#e0c79a 0%,rgba(200,170,120,0) 100%),radial-gradient(ellipse 60px 50px at 50px 40px,#d9742a 0%,rgba(60,40,30,0) 100%),radial-gradient(ellipse 70px 60px at 180px 150px,#5a5a5a 0%,rgba(30,30,30,0) 100%),linear-gradient(160deg,#2a2a2a,#121212 60%,#242424)"></div>
    <h3>DETAILING</h3>
  </article>
  <article class="abs service-card" style="left:445px">
    <div class="photo" role="img" aria-label="Gloved hands applying ceramic coating" style="background:radial-gradient(ellipse 110px 90px at 60px 50px,#c48a4a 0%,#6a4424 50%,rgba(30,25,20,0) 100%),radial-gradient(ellipse 120px 60px at 160px 150px,#3a3a3a 0%,rgba(20,20,20,0) 100%),linear-gradient(170deg,#3a2a1c,#151515 55%,#0c0c0c)"></div>
    <h3>CERAMIC COATING</h3>
  </article>
  <article class="abs service-card" style="left:784px">
    <div class="photo" role="img" aria-label="Luxury car dashboard and centre console" style="background:radial-gradient(ellipse 90px 60px at 60px 40px,#9a9a9a 0%,rgba(40,40,40,0) 100%),radial-gradient(ellipse 40px 110px at 140px 170px,#6a6a6a 0%,rgba(30,30,30,0) 100%),linear-gradient(160deg,#3a3a3a,#181818 55%,#2a2a2a)"></div>
    <h3>INTERIOR</h3>
  </article>
</section>

<section class="section about">
  <div class="photo about-bg" role="img" aria-label="Close-up of a dark sports car front wheel and headlight"></div>
  <div class="abs about-panel">
    <h2 class="heading">About Us</h2>
    <p>Lorem ipsum dolor sit amet, consectetur adipiscing elit, sed do eiusmod tempor incididunt ut labore et dolore magna aliqua. Ut enim ad minim veniam, quis nostrud exercitation ullamco laboris nisi ut aliquip ex ea commodo consequat. Duis aute irure dolor in repre henderit in voluptate velit esse</p>
    <a class="pill" href="#">Read More <span class="dot"><svg width="9" height="9" viewBox="0 0 10 10"><path d="M3 1.5 6.5 5 3 8.5" stroke="#111" stroke-width="2" fill="none"/></svg></span></a>
  </div>
</section>

<section class="section gallery">
  <h2 class="abs heading">Our Gallery</h2>
  <div class="photo tile" role="img" aria-label="Black sports coupe in a dark studio" style="left:111px;top:150px;width:580px;height:279px;background:radial-gradient(ellipse 230px 80px at 300px 160px,#4a4a4a 0%,#1c1c1c 55%,rgba(15,15,15,0) 100%),radial-gradient(ellipse 40px 10px at 470px 150px,#c0303a 0%,rgba(120,20,20,0) 100%),linear-gradient(150deg,#2a2a2a,#0d0d0d 60%,#161616)"></div>
  <div class="photo tile" role="img" aria-label="Car interior with tan leather seats" style="left:714px;top:150px;width:373px;height:279px;background:radial-gradient(ellipse 150px 90px at 260px 230px,#a8582c 0%,#6a3418 50%,rgba(30,20,15,0) 100%),radial-gradient(ellipse 160px 50px at 190px 20px,#7a6850 0%,rgba(40,30,20,0) 100%),linear-gradient(160deg,#3a3026,#161616 50%,#2a1a12)"></div>
  <div class="photo tile" role="img" aria-label="Pressure washing a car with foam" style="left:111px;top:445px;width:304px;height:278px;background:radial-gradient(ellipse 120px 90px at 120px 120px,#f4f4f4 0%,#d8d8d8 50%,rgba(180,180,180,0) 100%),radial-gradient(ellipse 40px 30px at 30px 30px,#4a9a9a 0%,rgba(100,150,150,0) 100%),linear-gradient(150deg,#bdbdbd,#cfcfcf 45%,#6a6a6a)"></div>
  <div class="photo tile" role="img" aria-label="Gloved hand polishing a car with a blue cloth" style="left:447px;top:445px;width:304px;height:278px;background:radial-gradient(ellipse 70px 50px at 140px 70px,#2f5fb8 0%,#1e3a78 50%,rgba(30,40,70,0) 100%),radial-gradient(ellipse 60px 120px at 240px 180px,#8a8a8a 0%,rgba(40,40,40,0) 100%),linear-gradient(150deg,#3a3a3a,#1a1a1a 50%,#101010)"></div>
  <div class="photo tile" role="img" aria-label="Applying protective film to a car bonnet" style="left:784px;top:445px;width:303px;height:278px;background:radial-gradient(ellipse 80px 50px at 80px 30px,#2a4aa0 0%,rgba(40,60,120,0) 100%),radial-gradient(ellipse 110px 60px at 150px 150px,#c8c8d0 0%,#5a5a6a 50%,rgba(30,30,40,0) 100%),linear-gradient(170deg,#e4e4e4,#3a3a44 45%,#14141c)"></div>
  <a class="abs pill gallery-cta" href="#">View More <span class="dot"><svg width="9" height="9" viewBox="0 0 10 10"><path d="M3 1.5 6.5 5 3 8.5" stroke="#111" stroke-width="2" fill="none"/></svg></span></a>
</section>

<section class="section lounge">
  <h2 class="abs heading">Client Lounge Area</h2>
  <p class="abs lead">Lorem ipsum dolor sit amet, consectetur adipiscing elit, sed do eiusmod tempor incididunt ut labore et dolore magna ali qua. Ut enim ad minim veniam,</p>
  <div class="abs amenity" style="top:217px"><span class="icon"></span><div><h3>Comfort</h3><p>Lorem ipsum dolor sit amet, consectetur adipiscing elit, sed do eiusmod tempor incididunt</p></div></div>
  <div class="abs amenity" style="top:337px"><span class="icon"></span><div><h3>Coffee</h3><p>Lorem ipsum dolor sit amet, consectetur adipiscing elit, sed do eiusmod tempor incididunt</p></div></div>
  <div class="abs amenity" style="top:450px"><span class="icon"></span><div><h3>Waiting Space</h3><p>Lorem ipsum dolor sit amet, consectetur adipiscing elit, sed do eiusmod tempor incididunt</p></div></div>
  <div class="photo lounge-photo" role="img" aria-label="Tan and navy leather lounge armchairs with a small side table"></div>
</section>

<section class="section testimonials">
  <div class="photo testimonials-bg" role="img" aria-label="Black and white close-up of a luxury car dashboard"></div>
  <div class="abs slide-arrow" style="left:549px;top:238px"><svg width="14" height="14" viewBox="0 0 20 20"><path d="M13 3 6 10l7 7" stroke="#111" stroke-width="3" fill="none"/></svg></div>
  <div class="abs slide-arrow" style="left:1078px;top:238px"><svg width="14" height="14" viewBox="0 0 20 20"><path d="M7 3l7 7-7 7" stroke="#111" stroke-width="3" fill="none"/></svg></div>
  <div class="abs quote-panel">
    <h2 class="heading">Testimonials</h2>
    <div class="stars">★★★★★</div>
    <span class="review-source"></span>
    <blockquote>Sed ut perspiciatis unde omnis iste natus error sit voluptatem accusantium doloremque laudantium, totam rem aperiam, eaque ipsa quae ab illo inventore veritatis et quasi architecto beatae vitae dicta sunt explicabo. Nemo enim ipsam voluptatem quia voluptas sit aspernatur aut odit aut fugit, sed quia consequuntur magni</blockquote>
    <div class="avatar">EM</div>
    <div class="reviewer"><strong>Elena Marsh</strong><span>MD at Northvale Group</span></div>
    <div class="quote-mark">”</div>
  </div>
</section>

<section class="section contact">
  <h2 class="abs heading">Contact Us</h2>
  <div class="abs field" style="top:204px">Name</div>
  <div class="abs field" style="top:262px">Phone Number</div>
  <div class="abs field" style="top:320px">E-Mail Address</div>
  <div class="abs field message" style="top:378px">Message</div>
  <a class="abs pill submit" href="#">Submit <span class="dot"><svg width="9" height="9" viewBox="0 0 10 10"><path d="M3 1.5 6.5 5 3 8.5" stroke="#111" stroke-width="2" fill="none"/></svg></span></a>
  <div class="abs map-ring"></div>
  <div class="abs map" role="img" aria-label="Map showing the Velour Detailing studio location"></div>
</section>

<footer class="section footer">
  <a class="brand" href="#"><span class="brand-mark"></span><span class="brand-name"><b>VELOUR</b><span>DETAILING</span></span></a>
  <ul class="nav">
    <li><a href="#">Home</a></li>
    <li><a href="#">About</a></li>
    <li><a href="#">Services</a></li>
    <li><a href="#">Gallery</a></li>
    <li><a href="#">Testimonials</a></li>
    <li><a href="#">Contact</a></li>
  </ul>
  <hr>
  <p class="copyright">Copyright © 2025 Velour Detailing. All rights reserved.</p>
</footer>

</body>
</html>
```